Etikett für Rotweinflasche
Liebe farbkosmos Atelier, wir werden uns bei der endgültigen Etikettengestaltung (finale Größe + Rückseite) noch an Euch melden. Bitte sendet uns euren Kontakt an helga.brandt@morvelli.wine
Zielgruppe
Morvelli Italia ist ein exklusives Boutique-Weingut in Sizilien, das hochqualitative Spitzenweine in kleinen Mengen mit modernster Technologie und stets nachhaltig erzeugt. Wir hinterfragen sowohl in der Agronomie im Weingarten als auch in der Önologie im Weinkeller alle herrschenden Traditionen und trachten danach, stets das beste Endprodukt zu kreieren. Der vulkanische, kalkreiche Boden Siziliens sowie trockene, sonnenreiche und niederschlagsarme Vegetationsperioden sind unsere optimale Basis.
Zielgruppe: Internationale Genussmenschen jeglichen Alters, die sich bewusst auch höherpreisige Weine (um die €30+) gönnen , vor allem kunstaffine young professionals mit Qualitäts-& Nachhaltigkeitsanspruch
Aufgabenstellung
Das Etikett ist für Rotwein-Flaschen (Cabernet Sauvignon / Nero D'Avola / Frappato / Syrah / Cerasuolo / Petit Verdot / sowie einen Bourdeaux-Cuveè aus Cabernet Sauvignon und Petit Verdot) .
Die Flasche ist reinschwarz, sehr hochwertig und schwer.
Flaschenform: Bordeauxflasche siehe technisches Datenblatt
Sleeve über dem Korken: schwarz mit weißer Schrift wie bisher
Zu gestalten ist das Etikett der Vorderseite. Zumindest die jeweilige Rotwein-Sorte ist auch textlich darzustellen (zwecks Scannen mit Trubel-App)
Der Kreativität kann freien Lauf gelassen werden! Unterscheidbarkeit vom Markt ist explizit gewollt.
Unsere aktuellen Etiketten und Markenauftritt siehe: https://morvelli.wine/shop/

```html
<!DOCTYPE html>
<html lang="de">
<head>
<meta charset="utf-8">
<title>Morvelli Sicilia – Etikett Cabernet Sauvignon</title>
<link rel="stylesheet" href="https://fonts.googleapis.com/css2?family=EB+Garamond:wght@400;500&display=swap">
<style>
  :root {
    --canvas-bg: #ffffff;
    --sleeve-black: #0d0d0d;
    --sleeve-edge: #1f1f1f;
    --label-mauve: #b37a72;
    --label-rose: #c9948c;
    --label-blush: #ecd3cc;
    --label-amber: #d2952f;
    --label-ochre: #b06e1c;
    --label-shadow: #5c3a2c;
    --type-light: #ffffff;
  }
  html, body {
    margin: 0;
    padding: 0;
    width: 849px;
    height: 1200px;
    overflow: hidden;
    background: var(--canvas-bg);
  }
  .canvas {
    position: relative;
    width: 849px;
    height: 1200px;
    font-family: "EB Garamond", Georgia, serif;
  }

  /* Kapsel / Sleeve über dem Korken */
  .capsule-sleeve {
    position: absolute;
    left: 80px;
    top: 106px;
    width: 238px;
    height: 476px;
    background: var(--sleeve-black);
    border-radius: 10px 10px 0 0;
  }
  .capsule-sleeve::before {
    content: "";
    position: absolute;
    left: 0;
    right: 0;
    top: 84px;
    height: 2px;
    background: var(--sleeve-edge);
  }
  .capsule-brand {
    position: absolute;
    left: 0;
    right: 0;
    top: 268px;
    margin: 0;
    text-align: center;
    color: var(--type-light);
    font-weight: 400;
  }
  .capsule-brand__name {
    display: block;
    font-size: 31px;
    letter-spacing: 0.02em;
    line-height: 1;
  }
  .capsule-brand__region {
    display: block;
    margin-top: 6px;
    font-size: 15px;
    letter-spacing: 0.22em;
    line-height: 1;
  }

  /* Vorderetikett */
  .front-label {
    position: absolute;
    left: 378px;
    top: 106px;
    width: 392px;
    height: 987px;
    overflow: hidden;
  }
  .label-artwork {
    position: absolute;
    inset: 0;
    background:
      radial-gradient(ellipse 38% 30% at 82% 48%, var(--label-amber) 0%, rgba(210,149,47,0) 100%),
      radial-gradient(ellipse 40% 28% at 80% 80%, var(--label-ochre) 0%, rgba(176,110,28,0) 100%),
      radial-gradient(ellipse 26% 40% at 14% 52%, var(--label-blush) 0%, rgba(236,211,204,0) 100%),
      radial-gradient(ellipse 20% 25% at 10% 88%, var(--label-blush) 0%, rgba(236,211,204,0) 100%),
      linear-gradient(180deg, var(--label-mauve) 0%, var(--label-rose) 28%, #a0704e 70%, var(--label-shadow) 100%);
  }
  .varietal-name {
    position: absolute;
    left: 0;
    right: 0;
    top: 52px;
    margin: 0;
    text-align: center;
    font-weight: 400;
    font-size: 20px;
    letter-spacing: 0.12em;
    line-height: 1;
    color: var(--type-light);
  }
</style>
</head>
<body>
  <main class="canvas">
    <section class="capsule-sleeve" aria-label="Kapsel">
      <p class="capsule-brand">
        <span class="capsule-brand__name">MORVELLI</span>
        <span class="capsule-brand__region">SICILIA</span>
      </p>
    </section>
    <section class="front-label">
      <div class="label-artwork" role="img" aria-label="Fotografie einer sizilianischen Marionette an Fäden vor unscharfem, ockerfarbenem Hintergrund"></div>
      <h1 class="varietal-name">CABERNET SAUVIGNON</h1>
    </section>
  </main>
</body>
</html>
```